Chiropractic Business Card

I need a business card designed to help me stand apart from my competition. I really like simple, clean designs that appear open and inviting. I would like the designs to incorporate the color blue, green, or both. I really like the attached picture because it highlights that I just don't treat "back pain" and it being a nice computer graphic helps show that I have a modern practice. "Modern practice" meaning merging technology and most current research in my patient care.

My information is:

Lyle Farwick, DC
Phone- (707) 555-0182
Email- drlylefarwick@mailnest.example
Website- www.brevincourtchiropractic.example
Address- 248 Tolliver Street, Sonoma, CA 95999

Jpeg and pdf attached of Brevincourt Chiropractic logo.
Updates

Atmosphere to be clean lines and solid colors to be have gradient fading, but don't want too much going on with the fading. Simple.

Target Market(s)

Active adults who are health conscious between the ages of 20-70

Industry/Entity Type

Computer

Colors
0455a3
85cae6

Requirements
Must have
• Change color of Brevincourt chiropractic logo (maroon) to fit the rest of the design.
Nice to have
• Can separate the running image from the black background to have it work with the design.

```html
<!DOCTYPE html>
<html lang="en">
<head>
<meta charset="utf-8">
<title>Brevincourt Chiropractic – Business Card</title>
<link rel="stylesheet" href="https://fonts.googleapis.com/css2?family=Exo+2:wght@400;500;600;700&display=swap">
<style>
  :root {
    --navy: #3c3f98;
    --navy-deep: #2f3287;
    --cyan: #00aeef;
    --white: #f4f5f7;
    --silver: #a9acb4;
    --backdrop: #d9d5d2;
    --ink-light: #ffffff;
  }
  * { box-sizing: border-box; margin: 0; padding: 0; }
  html, body { width: 1200px; height: 802px; overflow: hidden; }
  body {
    background: var(--backdrop);
    font-family: "Exo 2", sans-serif;
    position: relative;
  }
  .card {
    position: absolute;
    top: 246px;
    width: 540px;
    height: 309px;
    overflow: hidden;
    box-shadow: 0 6px 18px rgba(0,0,0,0.18);
  }
  .card--front { left: 40px; }
  .card--back  { left: 620px; }
  .card__art { position: absolute; inset: 0; width: 100%; height: 100%; }
  .text { position: absolute; color: var(--ink-light); white-space: nowrap; letter-spacing: 1px; }

  .brand {
    position: absolute;
    left: 230px; top: 78px; width: 290px;
    text-align: center;
    color: var(--navy);
    font-weight: 700;
    font-size: 27px;
    line-height: 1.1;
    text-transform: uppercase;
    letter-spacing: 1px;
  }
  .website-pill { left: 225px; top: 203px; font-size: 15px; letter-spacing: 0.6px; }
  .contact-row { display: flex; align-items: flex-start; gap: 12px; font-size: 15px; line-height: 1.25; }
  .contact-row svg { flex: none; }
  .contact--phone { left: 28px; top: 150px; }
  .contact--address { left: 28px; top: 206px; }
  .contact--email { right: 24px; top: 268px; font-size: 16px; }

  .holder-name { left: 205px; top: 34px; font-size: 19px; font-weight: 500; letter-spacing: 3px; text-transform: uppercase; }
  .holder-title { left: 205px; top: 60px; font-size: 13px; letter-spacing: 1.5px; }
  .holder-website { left: 205px; top: 150px; font-size: 16px; }
</style>
</head>
<body>

<section class="card card--front" aria-label="Card front">
  <svg class="card__art" viewBox="0 0 540 309" aria-hidden="true">
    <rect width="540" height="309" fill="var(--navy)"/>
    <path d="M0 36 H540 V206 H232 Q212 206 207 188 L201 146 Q197 128 178 128 H0 Z"
          fill="var(--white)" stroke="var(--silver)" stroke-width="6"/>
    <rect x="206" y="190" width="310" height="48" rx="18" fill="var(--cyan)"/>
  </svg>

  <div class="brand">Brevincourt<br>Chiropractic</div>
  <div class="text website-pill">www.brevincourtchiropractic.example</div>

  <div class="text contact-row contact--phone">
    <svg width="16" height="18" viewBox="0 0 16 18"><path d="M4 1 L7 5 L5 7 Q7 11 10 13 L12 11 L15 14 L12 17 Q3 14 1 4 Z" fill="none" stroke="#fff" stroke-width="1.5"/></svg>
    <span>(707) 555-0182<br>(707) 555-0182</span>
  </div>

  <div class="text contact-row contact--address">
    <svg width="20" height="18" viewBox="0 0 20 18"><path d="M2 9 L10 2 L18 9 M4 8 V16 H8 V11 H12 V16 H16 V8" fill="none" stroke="#fff" stroke-width="1.6"/></svg>
    <span>248 Tolliver Street<br>Sonoma, CA 95999</span>
  </div>

  <div class="text contact-row contact--email">
    <svg width="24" height="17" viewBox="0 0 24 17"><rect x="1" y="1" width="22" height="15" fill="none" stroke="#fff" stroke-width="1.3"/><path d="M1 1 L12 10 L23 1 M1 16 L9 8 M23 16 L15 8" fill="none" stroke="#fff" stroke-width="1.1"/></svg>
    <span>drlylefarwick@mailnest.example</span>
  </div>
</section>

<section class="card card--back" aria-label="Card back">
  <svg class="card__art" viewBox="0 0 540 309" aria-hidden="true">
    <rect width="540" height="309" fill="var(--navy)"/>
    <path d="M0 0 H100 Q124 0 128 22 L138 118 Q142 140 164 142 H172 V309 H0 Z"
          fill="var(--cyan)" stroke="var(--silver)" stroke-width="6"/>
    <path d="M0 0 H100 Q124 0 128 22 L138 118 Q142 140 164 142 H172 V190 H0 Z"
          fill="var(--white)" opacity="0.9"/>
    <path d="M0 190 H172" stroke="var(--cyan)" stroke-width="2"/>
  </svg>

  <div class="text holder-name">Lyle Farwick, DC</div>
  <div class="text holder-title">Chiropractor</div>
  <div class="text holder-website">www.brevincourtchiropractic.example</div>
</section>

</body>
</html>
```